Varnex Consulting Business card design.

See our website www.varnexconsulting.example which will give you a good idea of what we are about. The font is called 'Play'.

I'd like a standout business card in keeping with the themes and branding on the website

Target Market(s)

professionals. HR directors

Industry/Entity Type

Business

Contact Information for Business Card

Varnex Consulting PO Box 3172 Merrowdale NSW 2291 1300 485 193 Gavin Threlkeld Principal email: career@varnexconsulting.example ABN: 71203948865

Font styles to use
Other font styles liked:
• Play

Requirements
Must have
• Must have same design colours and branding as website.
• On back I'd prefer a list of the things we do which appears below the name at the header on the website

```html
<!DOCTYPE html>
<html lang="en">
<head>
<meta charset="utf-8">
<title>Varnex Consulting – Business Card</title>
<link href="https://fonts.googleapis.com/css2?family=Play:wght@400;700&display=swap" rel="stylesheet">
<style>
  :root{
    --page:#e9e6e1;
    --navy-deep:#071a2c;
    --navy:#0f3353;
    --navy-light:#1d4f76;
    --sky:#3fb3e6;
    --sky-soft:#7fcdf0;
    --white:#ffffff;
    --band:rgba(255,255,255,0.82);
    --ink:#2b3640;
    --ink-soft:#6d7882;
  }
  *{box-sizing:border-box;margin:0;padding:0}
  html,body{width:1200px;height:902px;overflow:hidden}
  body{background:var(--page);font-family:'Play',sans-serif;position:relative}

  .card{position:absolute;width:620px;height:379px;border-radius:4px;overflow:hidden;
        box-shadow:0 14px 30px rgba(0,0,0,0.22),0 2px 5px rgba(0,0,0,0.15)}

  /* front */
  .card--front{left:110px;top:50px}
  .front__photo{position:absolute;inset:0;
    background:linear-gradient(170deg,#0d63c9 0%,#2d8fe6 35%,#8cc6f0 58%,#e9f4fb 72%,#ffffff 82%,#cfe6f6 100%)}
  .front__band{position:absolute;left:0;right:0;top:222px;height:86px;background:var(--band);
    display:flex;flex-direction:column;justify-content:center;padding-left:70px}
  .front__name{font-size:40px;letter-spacing:1px;color:var(--ink);line-height:1}
  .front__services{font-size:12.5px;color:var(--ink-soft);letter-spacing:.6px;margin-top:8px}

  /* back */
  .card--back{left:470px;top:470px;
    background:radial-gradient(ellipse at 35% 30%,var(--navy-light) 0%,var(--navy) 45%,var(--navy-deep) 100%)}
  .back__brand{position:absolute;left:40px;top:56px}
  .back__name{font-size:44px;letter-spacing:1px;color:var(--white);line-height:1}
  .back__services{font-size:13px;color:var(--sky);letter-spacing:.6px;margin-top:10px}
  .back__rule{position:absolute;height:1.5px;background:var(--white);opacity:.85}
  .back__rule--left{left:0;top:150px;width:330px}
  .back__rule--right{right:0;top:150px;width:50px}
  .back__person{position:absolute;right:62px;top:126px;text-align:right}
  .person__name{font-size:26px;font-weight:700;color:var(--sky);line-height:1}
  .person__role{font-size:17px;font-weight:700;color:var(--white);margin-top:4px}
  .back__rule--base{left:0;right:0;top:228px;height:1px;opacity:.5}
  .back__contact{position:absolute;left:40px;top:250px;color:var(--white)}
  .contact__abn{font-size:19px;margin-bottom:10px}
  .contact__list{list-style:none}
  .contact__item{display:flex;align-items:center;gap:10px;font-size:15px;line-height:25px}
  .contact__icon{width:15px;height:15px;flex:none}
</style>
</head>
<body>

<section class="card card--front" aria-label="Card front">
  <div class="front__photo" role="img" aria-label="Snowboarder mid-air above a snowy mountain peak against a bright blue sky"></div>
  <div class="front__band">
    <h1 class="front__name">VARNEX CONSULTING</h1>
    <p class="front__services">Search &amp; Select | Career | Coaching | Leadership | Outplacement</p>
  </div>
</section>

<section class="card card--back" aria-label="Card back">
  <div class="back__brand">
    <h2 class="back__name">VARNEX CONSULTING</h2>
    <p class="back__services">Search &amp; Select | Career | Coaching | Leadership | Outplacement</p>
  </div>
  <div class="back__rule back__rule--left"></div>
  <div class="back__rule back__rule--right"></div>
  <div class="back__person">
    <p class="person__name">Gavin Threlkeld</p>
    <p class="person__role">Principal</p>
  </div>
  <div class="back__contact">
    <p class="contact__abn">ABN: 71203948865</p>
    <ul class="contact__list">
      <li class="contact__item">
        <svg class="contact__icon" viewBox="0 0 16 16" aria-hidden="true"><rect width="16" height="16" rx="2" fill="var(--sky)"/><path d="M4 5.5c0-1 .8-1.5 1.5-1.5h5c.7 0 1.5.5 1.5 1.5v.8H9.8v-.8H6.2v.8H4zM4.5 7.5h7l.5 4.5H4z" fill="var(--navy-deep)"/></svg>
        1300 485 193
      </li>
      <li class="contact__item">
        <svg class="contact__icon" viewBox="0 0 16 16" aria-hidden="true"><rect width="16" height="16" rx="2" fill="var(--sky)"/><rect x="3.5" y="5" width="9" height="6.5" fill="none" stroke="var(--navy-deep)" stroke-width="1.2"/><path d="M3.5 5l4.5 3.6L12.5 5" fill="none" stroke="var(--navy-deep)" stroke-width="1.2"/></svg>
        career@varnexconsulting.example
      </li>
      <li class="contact__item">
        <svg class="contact__icon" viewBox="0 0 16 16" aria-hidden="true"><rect width="16" height="16" rx="2" fill="var(--sky)"/><path d="M8 3.5a3 3 0 0 1 3 3c0 2.2-3 5.8-3 5.8S5 8.7 5 6.5a3 3 0 0 1 3-3z" fill="var(--navy-deep)"/><circle cx="8" cy="6.5" r="1.1" fill="var(--sky)"/></svg>
        PO Box 3172 Merrowdale NSW 2291
      </li>
    </ul>
  </div>
</section>

</body>
</html>
```